Mira Ellsworth ADHD coach needs a flyer

I need a flyer to be sent by email. the copy is attached. It can be changed/reduced to fit the flyer. I would like to keep my website colors. My website is www.miraellsworth.net - Thank you!

```html
<!DOCTYPE html>
<html lang="en">
<head>
<meta charset="utf-8">
<title>Mira Ellsworth – ADHD and Academic Coach</title>
<link rel="stylesheet" href="https://fonts.googleapis.com/css2?family=Oswald:wght@200;300&family=Montserrat:wght@700;800&family=Nunito+Sans:ital,wght@0,300;0,400;0,700;1,300;1,400&display=swap">
<style>
:root{
  --slate:#9fb3bf;
  --slate-mid:#b4c4cd;
  --mist:#dae5ea;
  --band:#c9d6dc;
  --ink:#2c2c2c;
  --body:#3a3a3a;
  --charcoal:#6a6a6a;
  --white:#ffffff;
}
*{margin:0;padding:0;box-sizing:border-box}
html,body{width:840px;height:1200px;overflow:hidden;background:var(--white)}
body{font-family:"Nunito Sans",Arial,sans-serif;color:var(--body);position:relative}
.flyer{position:absolute;inset:0;width:840px;height:1200px}
.abs{position:absolute}

/* header */
.name-block{left:0;top:0;width:280px;height:140px;background:var(--mist);padding:16px 0 0 38px}
.name{font-family:"Oswald",sans-serif;font-weight:200;font-size:58px;line-height:56px;color:var(--slate);letter-spacing:1px;text-transform:uppercase}
.headline-block{left:280px;top:0;width:560px;height:140px;background:var(--slate);padding:26px 0 0 30px}
.headline{font-family:"Montserrat",sans-serif;font-weight:800;font-size:21.5px;line-height:29px;color:var(--white)}
.chevrons{display:block}
.credentials{left:0;top:140px;width:280px;height:27px;font-family:"Oswald",sans-serif;font-weight:300;font-size:15px;color:var(--ink);padding:4px 0 0 39px}

/* photos */
.photo{overflow:hidden}
.photo-portrait{left:0;top:167px;width:280px;height:404px;background:linear-gradient(180deg,#aab6bd 0%,#b7c1c6 40%,#e9cfcf 70%,#f0d6d6 100%)}
.photo-group{left:280px;top:390px;width:560px;height:181px;background:linear-gradient(180deg,#cfd9c8 0%,#b99c7d 55%,#7a5436 100%)}
.photo-study{left:280px;top:576px;width:560px;height:251px;background:linear-gradient(120deg,#eef0f2 0%,#d9dde2 45%,#b9bfc8 100%)}
.photo-library{left:0;top:946px;width:280px;height:225px;background:linear-gradient(160deg,#e8e6e4 0%,#c9c3c2 50%,#6b6461 100%)}

/* intro */
.intro{top:177px;font-size:10.2px;line-height:12.9px;font-weight:300;color:var(--body)}
.intro-left{left:309px;width:216px}
.intro-right{left:558px;width:252px}
.lede{font-weight:700;color:var(--ink);margin-bottom:13px}

/* empowering */
.section-title{font-family:"Montserrat",sans-serif;font-weight:800;font-size:13.5px;color:var(--ink);text-transform:uppercase;line-height:16px}
.section-sub{font-style:italic;font-weight:400;font-size:13px;text-transform:uppercase;line-height:16px;color:var(--ink)}
.empower{left:33px;top:623px;width:235px;font-size:9.6px;line-height:12px;font-weight:300}
.empower p{margin-top:8px}
.empower .section-title{margin-bottom:0}
.empower .section-sub{text-transform:none}
ul.dots{list-style:none;margin-top:5px}
ul.dots li{position:relative;padding-left:16px;margin-bottom:5px}
ul.dots li::before{content:"";position:absolute;left:2px;top:4px;width:4px;height:4px;border-radius:50%;background:var(--ink)}

/* lower panels */
.panel-potential{left:280px;top:827px;width:280px;height:344px;background:var(--slate)}
.band-title{background:var(--band);padding:10px 18px;color:var(--ink)}
.band-title .section-sub{font-weight:300;font-size:12.5px}
.panel-potential ul{padding:10px 18px 0 17px;font-size:9.6px;line-height:11.5px;font-weight:300;color:var(--ink)}
.band-plain{font-family:"Montserrat",sans-serif;font-weight:700;font-size:12.5px;color:var(--ink);background:var(--band);padding:5px 17px;margin-top:4px}
.panel-voices{left:560px;top:827px;width:280px;height:255px;background:var(--slate)}
.voice-title{font-family:"Montserrat",sans-serif;font-weight:700;font-size:12.5px;color:var(--ink);background:var(--band);padding:5px 19px}
.quotes{padding:9px 19px 6px;font-size:8.6px;line-height:10.5px;font-weight:300;color:var(--ink)}
.quotes p{margin-bottom:8px}
.quotes em{font-style:italic}
.quotes.students{font-style:italic}
.next-steps{left:560px;top:1082px;width:280px;height:89px;background:var(--charcoal);color:var(--white);padding:12px 16px 0 48px}
.next-steps h3{font-family:"Montserrat",sans-serif;font-weight:700;font-size:13px;margin-bottom:4px}
.next-steps p{font-size:10px;line-height:12.5px;font-weight:300}
.next-steps strong{font-weight:700}
.next-icon{left:574px;top:1095px}
.footer{left:0;top:1171px;width:840px;height:29px;text-align:center;font-family:"Montserrat",sans-serif;font-weight:700;font-size:11px;color:var(--slate);padding-top:8px}
</style>
</head>
<body>
<main class="flyer">
  <header>
    <div class="abs name-block"><h1 class="name">Mira<br>Ellsworth</h1></div>
    <div class="abs headline-block">
      <h2 class="headline">Helping Your Child with ADHD or<br>Other Learning Challenges Thrive<br>in College and Beyond</h2>
      <svg class="abs chevrons" style="left:316px;top:116px" width="140" height="16" viewBox="0 0 140 16" fill="none" stroke="#fff" stroke-width="1.2">
        <path d="M2 2l6 6-6 6M11 2l6 6-6 6M24 2l6 6-6 6M33 2l6 6-6 6M50 2l6 6-6 6M59 2l6 6-6 6M68 2l6 6-6 6M77 2l6 6-6 6M93 2l6 6-6 6M102 2l6 6-6 6M111 2l6 6-6 6M120 2l6 6-6 6"/>
      </svg>
    </div>
    <p class="abs credentials">Ph.D. &nbsp;|&nbsp; ADHD and Academic Coach</p>
  </header>

  <div class="abs photo photo-portrait" role="img" aria-label="Portrait photo of Mira Ellsworth in a pale pink blazer, arms folded, against a grey wall"></div>

  <div class="abs intro intro-left">
    <p class="lede">Academic success coaching that leads to lifelong transformation for students with ADHD and similar challenges that may have impeded their ability to thrive.</p>
    <p>Sending your child off to college can feel scary, especially if that college is hundreds of miles away. You worry about how they'll do on their own—whether they'll make friends, earn good grades, and be happy—especially without you there to support them daily. You know your child is bright, and you want them to have a great future, but you're concerned they will struggle without the right support and resources.</p>
  </div>
  <div class="abs intro intro-right">
    <p>You don't need to feel helpless as you send your child off to this next stage of their lives. Mira is dedicated to making that transition easier for everyone. Mira Ellsworth has years of experience helping students thrive despite their challenges. She sees your child's potential and helps them see it, too. She provides a safety net as they adjust to a new environment at college. Her services are comprehensive and adaptable, based on the requirements of each individual: helping with course selection and scheduling, time management, study strategies, focus, making new friends, and adapting to change. Through it all, Mira guides students through fundamental work on mindset to ensure that changes stick.</p>
  </div>

  <div class="abs photo photo-group" role="img" aria-label="Photo of a row of smiling college students sitting on a wooden bench with laptops and tablets outdoors"></div>
  <div class="abs photo photo-study" role="img" aria-label="Photo of four students gathered around a table reviewing papers together"></div>

  <section class="abs empower">
    <svg width="140" height="16" viewBox="0 0 140 16" fill="none" stroke="#9fb3bf" stroke-width="1.2" style="display:block;margin:-27px 0 12px">
      <path d="M2 2l6 6-6 6M11 2l6 6-6 6M24 2l6 6-6 6M33 2l6 6-6 6M50 2l6 6-6 6M59 2l6 6-6 6M68 2l6 6-6 6M77 2l6 6-6 6M93 2l6 6-6 6M102 2l6 6-6 6M111 2l6 6-6 6M120 2l6 6-6 6"/>
    </svg>
    <h3 class="section-title">Empowering Focus:</h3>
    <p class="section-sub" style="margin-top:0;text-transform:uppercase">How Mira Helps</p>
    <p>Mira has taken students from failing to a 3.0 GPA, and from a C student to the Dean's List, in just one semester. It doesn't take years to provide lasting results; all it takes is the right guide.</p>
    <p>Uniquely positioned to help your child, Mira:</p>
    <ul class="dots">
      <li>Tailors support so that your child improves focus and maximizes their potential in college and beyond.</li>
      <li>Understands your child's unique needs - she sees the gifts that others often miss.</li>
      <li>Knows the academic landscape intimately, including the challenges faced by students with ADHD and other conditions.</li>
      <li>Helps with the logistics of scheduling in a way that most advisors can't, enrolling students in the courses that best suit their learning style.</li>
      <li>Nurtures the brilliance in your bright child.</li>
      <li>Provides a balance between encouraging students and challenging them.</li>
    </ul>
  </section>

  <div class="abs photo photo-library" role="img" aria-label="Photo of two students talking between library bookshelves, one holding an open book"></div>

  <section class="abs panel-potential">
    <div class="band-title">
      <h3 class="section-title">Realizing Potential:</h3>
      <p class="section-sub">The Transformation You'll See in Your Child</p>
    </div>
    <ul class="dots">
      <li>A mindset of self-belief and increased confidence.</li>
      <li>Higher grades and the drive to graduate.</li>
      <li>Social integration and making friends.</li>
      <li>Happiness and fulfilment.</li>
      <li>A deep sense of personal achievement and pride.</li>
    </ul>
    <h3 class="band-plain">You Will Have:</h3>
    <ul class="dots">
      <li>Less stress, knowing that your child is in good hands.</li>
      <li>Fewer sleepless nights worrying about your child.</li>
      <li>Confidence that they are receiving the right support.</li>
      <li>Joy and pride at seeing them do well.</li>
    </ul>
  </section>

  <section class="abs panel-voices">
    <h3 class="voice-title">What Parents Say</h3>
    <div class="quotes">
      <p>“Mira was the glue that kept our daughter in college… as our daughter's Academic Coach, [she] gave our daughter the ability to finish strong by empowering her with the skills needed to be successful.”—<em>Renee</em></p>
      <p>“Mira has always told my daughter not that she <em>can</em> succeed, but that she <em>will</em> succeed.”—<em>Paula</em></p>
    </div>
    <h3 class="voice-title">What Students Say</h3>
    <div class="quotes">
      <p><em>"Last semester I completed all 16 hours and I had the highest GPA I've ever had!" —Former student</em></p>
      <p>“Under her instruction, my grades began to improve. I ended up making the Dean's List during my time at Brookfield, and I was also inducted into Sigma Lambda Rho. I am currently in my first year of law school at Halden University, a top tier school.”—<em>Former student</em></p>
    </div>
  </section>

  <section class="abs next-steps">
    <h3>Next Steps</h3>
    <p>To learn more and discuss your child's individual needs, call <strong>555·014·2290</strong> or email <strong>coach@miraellsworth.net</strong></p>
  </section>
  <svg class="abs next-icon" width="30" height="20" viewBox="0 0 30 20" fill="none" stroke="#fff" stroke-width="1.4" aria-hidden="true">
    <path d="M2 2l8 8-8 8M13 2l8 8-8 8"/>
  </svg>

  <footer class="abs footer">www.miraellsworth.net</footer>
</main>
</body>
</html>
```